Business Card Re-Design/Update

We'd like to update out business cards. I've included our current "Style guide" which has the colour scheme of the organisation in it. I've also included the branding files with logos etc in them.

I've also included a copy of one of our existing cards so that you can see how ugly/dated they look. I'd like a fresh modern corporate look.

Target Market(s)

These are for our clients, potential clients, industry contacts - like all business cards

Contact Information for Business Card

Name
Position
Company Address - Level 1, 47 Fernby Street, Carlow Qld 4072
Direct Phone
mobile
Email
Website -www.korvalit.com.au
Logo

Colors

Designer to choose colors to be used in the design.

Requirements
Must have
• Main Logo
• Cards will need to be editable to be able to personalize them for each new employee.
Nice to have
• The MapOut, ShipWell, KeepSteady would be okay to have if they can be sensibly and professionally added to the look without detracting from the main imagery.
• Maybe they could go on the back of the card? will leave this to your creative discretion as to whether/where they fit.
Should not have
• Should not have decorative or script fonts

```html
<!DOCTYPE html>
<html lang="en">
<head>
<meta charset="utf-8">
<title>korvalIT business card</title>
<link href="https://fonts.googleapis.com/css2?family=Lato:wght@400;700;900&display=swap" rel="stylesheet">
<style>
  :root {
    --backdrop: #2b2b2d;
    --brand-red: #c8161d;
    --brand-red-dark: #a80f16;
    --card-white: #f4f4f4;
    --ink: #2a2a2a;
    --on-red: #ffffff;
    --on-red-soft: #f3c9cb;
  }
  * { box-sizing: border-box; margin: 0; padding: 0; }
  html, body { width: 1200px; height: 997px; overflow: hidden; }
  body {
    background: var(--backdrop);
    font-family: "Lato", Arial, sans-serif;
    position: relative;
  }
  .card {
    position: absolute;
    width: 580px;
    height: 331px;
    border-radius: 3px;
    overflow: hidden;
    box-shadow: 0 18px 40px rgba(0,0,0,.45);
  }

  /* Back of card */
  .card-back {
    left: 80px; top: 90px;
    background: linear-gradient(135deg, var(--brand-red) 0%, var(--brand-red-dark) 100%);
    display: flex; flex-direction: column; align-items: center; justify-content: center;
    gap: 26px;
  }
  .back-mark {
    display: flex; align-items: center; gap: 14px;
    color: var(--on-red);
    font-weight: 700;
    font-size: 40px;
  }
  .back-mark .mark-square { width: 30px; height: 30px; background: var(--on-red); }
  .back-url {
    color: var(--on-red);
    font-size: 13px;
    letter-spacing: 5px;
    text-transform: uppercase;
  }

  /* Front of card */
  .card-front {
    left: 540px; top: 520px;
    background: linear-gradient(135deg, var(--brand-red) 0%, var(--brand-red-dark) 100%);
  }
  .front-header {
    height: 128px;
    background: var(--card-white);
    display: flex; align-items: center; justify-content: center;
  }
  .brand-lockup {
    display: flex; align-items: center; gap: 14px;
    color: var(--ink);
    font-weight: 700;
    font-size: 46px;
    letter-spacing: -0.5px;
  }
  .brand-lockup .mark-square { width: 32px; height: 32px; background: var(--brand-red); }
  .header-rules {
    height: 18px;
    background: linear-gradient(
      var(--card-white) 0 3px,
      var(--brand-red) 3px 6px,
      var(--card-white) 6px 9px,
      var(--brand-red) 9px 12px,
      var(--card-white) 12px 15px,
      var(--brand-red) 15px 18px);
  }
  .front-body {
    display: flex;
    height: 185px;
    padding: 26px 28px 26px 28px;
  }
  .holder {
    flex: 1;
    text-align: right;
    padding-right: 26px;
    color: var(--on-red);
  }
  .holder-name { font-weight: 900; font-size: 16px; letter-spacing: .5px; text-transform: uppercase; }
  .holder-role { font-size: 12px; color: var(--on-red-soft); margin-top: 2px; }
  .holder-address { font-weight: 700; font-size: 14px; line-height: 1.35; margin-top: 30px; }
  .divider { width: 1px; background: linear-gradient(transparent, rgba(0,0,0,.45), transparent); }
  .contacts {
    flex: 1.15;
    list-style: none;
    padding-left: 26px;
    color: var(--on-red);
    font-size: 13.5px;
    display: flex; flex-direction: column; gap: 9px;
  }
  .contacts li { display: flex; align-items: center; gap: 12px; white-space: nowrap; }
  .contacts svg { width: 13px; height: 13px; fill: var(--on-red); flex: none; }
  .contacts .note { font-size: 11px; color: var(--on-red-soft); margin-left: 4px; }
</style>
</head>
<body>

<section class="card card-back" aria-label="Card back">
  <div class="back-mark"><span class="mark-square"></span><span>korvalIT</span></div>
  <p class="back-url">www.korvalit.com.au</p>
</section>

<section class="card card-front" aria-label="Card front">
  <header class="front-header">
    <div class="brand-lockup"><span class="mark-square"></span><span>korvalIT</span></div>
  </header>
  <div class="header-rules"></div>
  <div class="front-body">
    <div class="holder">
      <p class="holder-name">Dana Whitmore</p>
      <p class="holder-role">Business Development Manager</p>
      <p class="holder-address">12/58 Carrow Lane<br>Brenley QLD 4011</p>
    </div>
    <div class="divider"></div>
    <ul class="contacts">
      <li>
        <svg viewBox="0 0 16 16" aria-hidden="true"><rect x="4" y="1" width="8" height="14" rx="1.5"/></svg>
        +61 (0)412 555 018
      </li>
      <li>
        <svg viewBox="0 0 16 16" aria-hidden="true"><rect x="4" y="1" width="8" height="4"/><rect x="1" y="5" width="14" height="7" rx="1"/><rect x="4" y="10" width="8" height="5"/></svg>
        +61 (0)7 3010 5527
      </li>
      <li>
        <svg viewBox="0 0 16 16" aria-hidden="true"><path d="M3 1l3 3-1.5 2a9 9 0 0 0 5.5 5.5L12 10l3 3-2 2C7 15 1 9 1 3z"/></svg>
        <span>+61 (0)7 3010 5540<span class="note">(Direct)</span></span>
      </li>
      <li>
        <svg viewBox="0 0 16 16" aria-hidden="true"><path d="M1 3h14v10H1z M1 3l7 6 7-6" fill="none" stroke="#fff" stroke-width="1.5"/></svg>
        dwhitmore@korvalit.com.au
      </li>
    </ul>
  </div>
</section>

</body>
</html>
```